Stonebrace Business Card Design

The Stonebrace Co is an aggregate (crushing) equipment dealer serving Western Canadian provinces. Stonebrace is a distributor of aggregate equipment for different manufacturers.

We are looking to change and update the existing business card which has been used since the existence of the company. A copy of existing card has been attached for reference. The Stonebrace Co logo we want to remain the same and we want the green color to remain the same.

We are wanting something new with a different look. A refreshing card to show a new modern and updated look. No longer wanting to have the manufacturers on the back of the card but something more like our logo on the back of the card with a statement like "Crushing Solutions"

ideas could be:
- card can be different colors on front and back
- front or reverse of the card could possibly be the green color with the logo in black

Target Market(s)

Owners of Aggregate/Crushing companies

Contact Information for Business Card

see above

Requirements
Must have
• - logo to remain same along with same font within logo
• - green color to remain same
Nice to have
• as noted above under project description
Should not have

```html
<!DOCTYPE html>
<html lang="en">
<head>
<meta charset="utf-8">
<title>The Stonebrace Co – Business Card</title>
<link href="https://fonts.googleapis.com/css2?family=Montserrat:wght@400;500;700;800&display=swap" rel="stylesheet">
<style>
  :root {
    --olive: #918c36;
    --charcoal: #231f20;
    --white: #ffffff;
    --ink: #231f20;
    --backdrop: #e3e3e1;
    --muted: #3a3a3a;
  }
  * { box-sizing: border-box; margin: 0; padding: 0; }
  html, body {
    width: 1200px; height: 1000px; overflow: hidden;
    background: var(--backdrop);
    font-family: "Montserrat", Arial, sans-serif;
  }
  .sheet {
    width: 1200px; height: 1000px;
    display: flex; flex-direction: column; align-items: center; justify-content: center;
    gap: 60px;
  }
  .card {
    width: 700px; height: 400px; position: relative; overflow: hidden;
    box-shadow: 0 2px 10px rgba(0,0,0,.12);
  }

  /* Front */
  .card--front { background: var(--white); }
  .front-frame {
    position: absolute; inset: 36px 40px;
    border: 2px solid var(--olive);
  }
  .front-logo {
    position: absolute; left: 0; right: 0; top: 120px;
    display: flex; align-items: center; justify-content: center; gap: 20px;
  }
  .logo-dot { width: 56px; height: 56px; border-radius: 50%; background: var(--olive); flex: none; }
  .logo-name {
    font-weight: 800; font-size: 36px; letter-spacing: .5px; color: var(--ink);
    text-transform: uppercase; white-space: nowrap;
  }
  .front-tagline {
    position: absolute; left: 50%; bottom: 26px; transform: translateX(-50%);
    background: var(--white); padding: 0 22px;
    font-weight: 400; font-size: 21px; letter-spacing: 1.5px; color: var(--muted);
    text-transform: uppercase; white-space: nowrap;
  }

  /* Back */
  .card--back { display: flex; }
  .back-brand {
    width: 340px; background: var(--olive); color: var(--white);
    display: flex; flex-direction: column; justify-content: center;
    padding: 0 0 0 0;
  }
  .back-logo {
    display: flex; align-items: center; gap: 12px; padding: 0 24px;
  }
  .back-logo .logo-dot { width: 34px; height: 34px; background: var(--white); }
  .back-logo .logo-name { color: var(--white); font-size: 21px; font-weight: 800; }
  .back-rule { height: 1.5px; background: var(--white); margin: 22px 0 16px; }
  .back-lines {
    padding: 0 24px; font-size: 13.5px; letter-spacing: 1px; text-transform: uppercase;
    display: flex; gap: 8px; align-items: center; white-space: nowrap;
  }
  .back-lines .sep { width: 1.5px; height: 18px; background: var(--white); }

  .back-contact {
    flex: 1; background: var(--charcoal); color: var(--white);
    padding: 34px 0 0;
  }
  .contact-name {
    padding: 0 30px; font-size: 27px; font-weight: 500; letter-spacing: 1px; text-transform: uppercase;
  }
  .contact-rule { height: 1.5px; background: var(--white); margin: 14px 0 16px; }
  .contact-list { list-style: none; padding: 0 34px; }
  .contact-item {
    display: flex; align-items: center; gap: 18px; height: 31px;
    font-size: 17px; letter-spacing: .5px;
  }
  .contact-item svg { width: 18px; height: 18px; fill: var(--white); flex: none; }
  .contact-address {
    padding: 0 34px; font-size: 15px; line-height: 1.55; letter-spacing: .5px; text-transform: uppercase;
  }
</style>
</head>
<body>
<main class="sheet">

  <section class="card card--front" aria-label="Card front">
    <div class="front-frame"></div>
    <div class="front-logo">
      <span class="logo-dot"></span>
      <span class="logo-name">The Stonebrace Co.</span>
    </div>
    <p class="front-tagline">Crushing Solutions</p>
  </section>

  <section class="card card--back" aria-label="Card back">
    <div class="back-brand">
      <div class="back-logo">
        <span class="logo-dot"></span>
        <span class="logo-name">The Stonebrace Co.</span>
      </div>
      <div class="back-rule"></div>
      <p class="back-lines">
        <span>Screeners</span><span class="sep"></span>
        <span>Crushers</span><span class="sep"></span>
        <span>Stackers</span>
      </p>
    </div>

    <div class="back-contact">
      <h1 class="contact-name">Dana Holtby</h1>
      <div class="contact-rule"></div>
      <ul class="contact-list">
        <li class="contact-item">
          <svg viewBox="0 0 24 24" aria-hidden="true"><path d="M3 8c0-2 4-4 9-4s9 2 9 4v2h-5V8H8v2H3z"/><path d="M6 12h12l2 8H4z"/></svg>
          <span>780 . 555 . 0123</span>
        </li>
        <li class="contact-item">
          <svg viewBox="0 0 24 24" aria-hidden="true"><path d="M6.6 10.8a15 15 0 006.6 6.6l2.2-2.2c.3-.3.7-.4 1-.2 1.1.4 2.3.6 3.6.6.6 0 1 .4 1 1V20c0 .6-.4 1-1 1A17 17 0 013 4c0-.6.4-1 1-1h3.5c.6 0 1 .4 1 1 0 1.3.2 2.5.6 3.6.1.3 0 .7-.2 1z"/></svg>
          <span>780 . 555 . 0147</span>
        </li>
        <li class="contact-item">
          <svg viewBox="0 0 24 24" aria-hidden="true"><path d="M6 3h10l2 2v4H6z"/><path d="M3 10h18v8h-3v-3H6v3H3z"/><path d="M7 16h10v5H7z"/></svg>
          <span>780 . 555 . 0182</span>
        </li>
        <li class="contact-item">
          <svg viewBox="0 0 24 24" aria-hidden="true"><path d="M2 5h20v14H2z M3.5 6.5L12 13l8.5-6.5" fill="none" stroke="#fff" stroke-width="0"/><path d="M2 5h20L12 13z"/><path d="M2 7l10 8 10-8v12H2z"/></svg>
          <span>dana@stonebrace.ca</span>
        </li>
        <li class="contact-item">
          <svg viewBox="0 0 24 24" aria-hidden="true"><circle cx="12" cy="12" r="9" fill="none" stroke="#fff" stroke-width="2"/><ellipse cx="12" cy="12" rx="4" ry="9" fill="none" stroke="#fff" stroke-width="1.6"/><path d="M3 12h18M4.5 7.5h15M4.5 16.5h15" stroke="#fff" stroke-width="1.6"/></svg>
          <span>www.stonebrace.ca</span>
        </li>
      </ul>
      <div class="contact-rule"></div>
      <address class="contact-address" style="font-style:normal">
        2210-48B Avenue,<br>Nisku, Alberta T9E 1K3
      </address>
    </div>
  </section>

</main>
</body>
</html>
```